Briloran Clear Springs needs a new business card design (we produce and sell pure bottled water)

We need a clean modern design for our new business cards, We have an existing logo which ultimately cannot be changed, however it could be slighty improved and the colours adjusted. We have this existing logo on all of our bottles, vehicles etc.

Our company slogan is "Clear from spring to every sip".
Along with our relevant company information
(Address, phone, website email etc) we will only be using names and not putting position titles for flexibilty.

We are looking for a clean, minimalist modern design.

You can view our website (if need of an update also!) to see our business.

Industry/Entity Type

Business

Contact Information for Business Card

Staff Name : XXXXXX XXXXXX
Address : 9/41 Tavenor St
Halden Rise QLD 4172
Staff Mobile Number : 04XX XXX XXX
Office Phone Number : 07 3918 2457
Staff Email Address : XXXX@brilorancleargo.com.au
Website : www.brilorancleargo.com.au

Font styles to use
Sans Serif

Colors
cee9f5
33a6d7
0492cd
0455a3
3276b5
85abd2
cedeed

Requirements
Must have
• The ability to edit and change the staff members details as we will need to edit for each respective staff member (7 in total)

```html
<!DOCTYPE html>
<html lang="en">
<head>
<meta charset="utf-8">
<title>Briloran Clear Springs – Business Card</title>
<link rel="stylesheet" href="https://fonts.googleapis.com/css2?family=Source+Sans+3:wght@400;600;700;800&display=swap">
<style>
  :root {
    --backdrop: #141414;
    --paper: #ffffff;
    --brand-navy: #14129b;
    --brand-blue: #1a14a6;
    --stripe-soft: #e4e3f3;
    --stripe-dark: #2119ad;
    --ink: #1c1c2a;
    --on-blue: #ffffff;
  }
  * { box-sizing: border-box; margin: 0; padding: 0; }
  html, body {
    width: 1200px; height: 900px; overflow: hidden;
    background: var(--backdrop);
    font-family: "Source Sans 3", "Myriad Pro", Arial, sans-serif;
  }
  .stage { position: relative; width: 1200px; height: 900px; }
  .card {
    position: absolute; top: 170px; width: 347px; height: 561px; overflow: hidden;
  }
  .card__stripes { position: absolute; inset: 0; }
  .card--front { left: 259px; background: var(--paper); }
  .card--back { left: 631px; background: var(--brand-blue); }

  .brand-name {
    position: absolute; left: 0; width: 100%; text-align: center;
    font-weight: 800; text-transform: uppercase; line-height: 1;
  }
  .card--front .brand-name { top: 205px; color: var(--brand-navy); }
  .card--back .brand-name { top: 250px; color: var(--on-blue); }
  .brand-name__top { display: block; font-size: 46px; letter-spacing: 0.5px; }
  .brand-name__bottom { display: block; font-size: 25px; letter-spacing: 1px; margin-top: 4px; }

  .staff-name {
    position: absolute; top: 373px; left: 0; width: 100%; text-align: center;
    color: var(--brand-navy); font-weight: 600; font-size: 19px; letter-spacing: 0.3px;
  }
  .contact {
    position: absolute; top: 417px; left: 0; width: 100%; text-align: center;
    list-style: none; color: var(--ink); font-size: 15.5px; line-height: 23.5px;
  }
  .contact b { color: var(--brand-navy); font-weight: 700; }
  .contact .contact__web { color: var(--brand-navy); font-weight: 600; }
  .address {
    position: absolute; top: 502px; left: 0; width: 100%; text-align: center;
    color: var(--ink); font-size: 15.5px;
  }
  .slogan {
    position: absolute; top: 412px; left: 0; width: 100%; text-align: center;
    color: var(--on-blue); font-weight: 600; font-size: 26px; line-height: 42px;
    text-transform: uppercase;
  }
</style>
</head>
<body>
<main class="stage">
  <section class="card card--front" aria-label="Card front">
    <svg class="card__stripes" width="347" height="561" viewBox="0 0 347 561" aria-hidden="true">
      <g fill="var(--stripe-soft)">
        <polygon points="0,0 20,0 0,45"/>
        <polygon points="30,0 42,0 0,95 0,68"/>
        <polygon points="52,0 64,0 0,145 0,118"/>
        <polygon points="76,0 84,0 0,190 0,172"/>
        <polygon points="110,0 116,0 0,262 0,249"/>
        <polygon points="347,370 347,400 256,561 226,561"/>
        <polygon points="347,420 347,440 280,561 260,561"/>
        <polygon points="347,455 347,475 300,561 280,561"/>
        <polygon points="347,490 347,510 320,561 300,561"/>
        <polygon points="347,525 347,545 338,561 318,561"/>
      </g>
    </svg>
    <h1 class="brand-name">
      <span class="brand-name__top">Briloran</span>
      <span class="brand-name__bottom">Clear Springs</span>
    </h1>
    <p class="staff-name">MARCUS DELANE</p>
    <ul class="contact">
      <li><b>P:</b> 0400 582 913&nbsp; <b>M:</b> 07 3918 2457</li>
      <li><b>E:</b> info@brilorancleargo.com.au</li>
      <li class="contact__web">www.brilorancleargo.com.au</li>
    </ul>
    <p class="address">9/41 Tavenor St Halden Rise QLD 4172</p>
  </section>

  <section class="card card--back" aria-label="Card back">
    <svg class="card__stripes" width="347" height="561" viewBox="0 0 347 561" aria-hidden="true">
      <g fill="var(--stripe-dark)">
        <polygon points="0,60 40,0 70,0 0,105"/>
        <polygon points="90,0 110,0 0,165 0,135"/>
        <polygon points="200,0 230,0 0,345 0,300"/>
        <polygon points="347,150 347,195 105,561 75,561"/>
        <polygon points="347,260 347,290 148,561 125,561"/>
        <polygon points="347,380 347,420 228,561 195,561"/>
      </g>
    </svg>
    <h2 class="brand-name">
      <span class="brand-name__top">Briloran</span>
      <span class="brand-name__bottom">Clear Springs</span>
    </h2>
    <p class="slogan">Clear from spring<br>to every sip</p>
  </section>
</main>
</body>
</html>
```